Veranix - Solution provider in business consulting

Veranix is a swiss based company providing solutions for developing markets. The business covers various fields of business consulting, such as supply chain, product costs, quality management and manufacturing management. The Business operates in a efficient, straight and solution oriented manner.
The final design should communicate these characteristics. Asian people as well as as western people shall identify the qualities of the company at first sight.
The customer needs business cards with a simple view but an recognizable design, printed in high quality. Engraved elements such as the globe or simple words are possible.
Available colors are: (RAL)
102/102/102
51/102/102
153/204/153
255/102/51
Font: Calibri

```html
<!DOCTYPE html>
<html lang="en">
<head>
<meta charset="utf-8">
<title>Veranix business card</title>
<link rel="stylesheet" href="https://fonts.googleapis.com/css2?family=Open+Sans:wght@400;700&display=swap">
<style>
  :root {
    --stage: #e6e4e1;
    --card-white: #ffffff;
    --card-black: #2a2a2a;
    --ink-grey: #666666;
    --ink-dark: #555555;
    --band-light: #8a8a8a;
    --band-dark: #5e5e5e;
    --paper-white: #ffffff;
  }
  * { box-sizing: border-box; margin: 0; padding: 0; }
  html, body {
    width: 1200px; height: 900px; overflow: hidden;
    background: var(--stage);
    font-family: "Open Sans", sans-serif;
  }
  .card {
    position: absolute; left: 290px;
    width: 620px; height: 365px;
    box-shadow: 0 4px 14px rgba(0,0,0,0.18);
    overflow: hidden;
  }
  .card-back { top: 45px; background: var(--card-black); }
  .card-front { top: 470px; background: var(--card-white); }

  .back-wordmark {
    position: absolute; inset: 0;
    display: flex; align-items: center; justify-content: center;
    color: var(--paper-white);
    font-size: 76px; font-weight: 400; letter-spacing: 1px;
  }

  .corner-mark { position: absolute; left: 0; top: 0; }
  .holder { position: absolute; left: 82px; top: 14px; color: var(--ink-dark); }
  .holder-name { font-size: 20px; font-weight: 700; line-height: 1.1; }
  .holder-title { font-size: 12px; line-height: 1.3; color: var(--ink-grey); }

  .address {
    position: absolute; left: 44px; top: 118px;
    font-size: 13px; line-height: 1.35; color: var(--ink-grey);
  }
  .contacts {
    position: absolute; left: 28px; top: 180px;
    list-style: none; font-size: 13px; color: var(--ink-grey);
  }
  .contacts li { display: flex; align-items: center; gap: 10px; height: 21px; }
  .contacts svg { width: 12px; height: 12px; flex: none; }

  .front-wordmark {
    position: absolute; left: 340px; top: 128px;
    color: var(--ink-grey);
    font-size: 62px; font-weight: 400; letter-spacing: 1px;
  }
  .bottom-band { position: absolute; left: 0; bottom: 0; }
</style>
</head>
<body>

<section class="card card-back">
  <div class="back-wordmark">Veranix</div>
</section>

<section class="card card-front">
  <svg class="corner-mark" width="70" height="50" viewBox="0 0 70 50">
    <rect x="0" y="0" width="66" height="48" fill="var(--band-light)"/>
    <polygon points="44,0 52,0 18,48 10,48" fill="var(--paper-white)"/>
    <polygon points="52,0 66,0 66,48 18,48" fill="var(--band-dark)"/>
  </svg>

  <div class="holder">
    <p class="holder-name">Lena Marbach</p>
    <p class="holder-title">CEO</p>
  </div>

  <p class="address">Veranix GmbH Feldweg 14<br>9200 Talwil Switzerland</p>

  <ul class="contacts">
    <li>
      <svg viewBox="0 0 12 12"><rect x="3" y="0.5" width="6" height="11" rx="1" fill="none" stroke="var(--ink-grey)" stroke-width="1.2"/><circle cx="6" cy="9.5" r="0.7" fill="var(--ink-grey)"/></svg>
      +41 79 555 0142
    </li>
    <li>
      <svg viewBox="0 0 12 12"><path d="M2.5 1 L4.5 1 L5.3 3.6 L4 4.6 C4.7 6.2 5.8 7.3 7.4 8 L8.4 6.7 L11 7.5 L11 9.5 C11 10.4 10.3 11 9.5 11 C5 10.6 1.4 7 1 2.5 C1 1.7 1.6 1 2.5 1 Z" fill="var(--ink-grey)"/></svg>
      +41 71 555 0187
    </li>
    <li>
      <svg viewBox="0 0 12 12"><rect x="0.5" y="2" width="11" height="8" fill="var(--ink-grey)"/><polyline points="0.5,2 6,6.5 11.5,2" fill="none" stroke="var(--paper-white)" stroke-width="1"/></svg>
      lena.marbach@veranix.ch
    </li>
    <li>
      <svg viewBox="0 0 12 12"><circle cx="6" cy="6" r="5.5" fill="var(--ink-grey)"/><path d="M1 6 H11 M6 0.5 C3.5 3 3.5 9 6 11.5 M6 0.5 C8.5 3 8.5 9 6 11.5" fill="none" stroke="var(--paper-white)" stroke-width="0.8"/></svg>
      www.veranix.ch
    </li>
  </ul>

  <div class="front-wordmark">Veranix</div>

  <svg class="bottom-band" width="620" height="40" viewBox="0 0 620 40">
    <polygon points="0,12 282,12 270,40 0,40" fill="var(--band-light)"/>
    <polygon points="292,12 620,12 620,40 280,40" fill="var(--band-dark)"/>
  </svg>
</section>

</body>
</html>
```